Maris Dovey Studio Business Cards

Hi - using the information and logo provided I require a two sided business card designed with the following information. The business card is a 'mini card' 3.5" x 1.25".

Front of card should be the logo attached but inverted (so the background is the peach colour and the logo white).

Back should have these details. If we can't fit the Pictogrum and Friendwall part can we just put the little logos.

Tessa Varnold

Art and Design Consultant
Dealer - Curator - Events - Styling - Creative Sourcing

P: 0438 217 604
E: tessa@marisdoveystudio.example
W: www.marisdoveystudio.example
I (pictogram image please): marisdoveystudio F (Friendwall image please): MarisDoveyAdviser

Target Market(s)

Galleries, artists, art buyers, interior design clients, event managers, creative types

Industry/Entity Type

Business

```html
<!DOCTYPE html>
<html lang="en">
<head>
<meta charset="utf-8">
<title>Maris Dovey Studio — Mini Business Cards</title>
<link rel="stylesheet" href="https://fonts.googleapis.com/css2?family=Marcellus&family=Tenor+Sans&display=swap">
<style>
  :root {
    --stage: #6a5950;
    --card-front: #1b1b1c;
    --card-front-glow: #3a3a3b;
    --card-back: #565758;
    --peach: #f2b8a0;
    --peach-faint: rgba(242, 184, 160, 0.16);
    --grey-type: #8a8a8a;
    --white: #f4f4f4;
    --rule: rgba(255, 255, 255, 0.14);
  }
  * { box-sizing: border-box; margin: 0; padding: 0; }
  html, body { width: 1200px; height: 960px; overflow: hidden; }
  body { background: var(--stage); position: relative; font-family: "Tenor Sans", sans-serif; }

  .card { position: absolute; width: 871px; height: 311px; overflow: hidden; }

  /* Front */
  .card--front {
    left: 34px; top: 64px;
    background: radial-gradient(ellipse 340px 230px at 50% 28%, var(--card-front-glow), var(--card-front) 70%);
  }
  .brand-mark {
    position: absolute; left: 50%; top: 22px; transform: translateX(-50%);
    width: 118px; height: 118px; border-radius: 50%; background: var(--peach);
  }
  .brand-name {
    position: absolute; left: 0; right: 0; top: 170px; text-align: center;
    font-family: "Marcellus", serif; font-size: 34px; letter-spacing: 5px;
    text-transform: uppercase; color: var(--peach);
  }
  .services {
    position: absolute; left: 0; right: 0; top: 255px; height: 40px;
    border-top: 1px solid var(--rule); border-bottom: 1px solid var(--rule);
    display: flex; align-items: center; justify-content: center;
    font-family: "Marcellus", serif; font-size: 23px; letter-spacing: 2.5px; color: var(--white);
  }
  .services span + span::before { content: "|"; margin: 0 10px; }

  /* Back */
  .card--back { left: 286px; top: 462px; background: var(--card-back); }
  .back-mark {
    position: absolute; right: 46px; top: 20px; width: 240px; height: 240px;
    border-radius: 50%; background: var(--peach-faint);
    display: flex; align-items: center; justify-content: center; text-align: center;
    font-family: "Marcellus", serif; font-size: 30px; line-height: 1.25; color: rgba(130, 150, 160, 0.45);
  }
  .holder-name {
    position: absolute; left: 35px; top: 22px;
    font-family: "Marcellus", serif; font-size: 42px; color: var(--peach);
  }
  .holder-title { position: absolute; left: 35px; top: 80px; font-size: 19px; color: var(--white); }
  .rule { position: absolute; left: 35px; height: 1px; background: var(--rule); }
  .rule--top { top: 112px; width: 440px; }
  .rule--social-top { top: 234px; width: 810px; }
  .rule--social-bottom { top: 280px; width: 810px; }

  .contact { position: absolute; left: 35px; top: 126px; }
  .contact-row { display: flex; height: 30px; align-items: center; font-size: 19px; }
  .contact-label { width: 98px; color: var(--peach); }
  .contact-value { color: var(--white); }

  .social { position: absolute; left: 46px; top: 238px; height: 42px; display: flex; align-items: center; font-size: 24px; color: var(--white); }
  .social-item { display: flex; align-items: center; }
  .social-icon { width: 36px; height: 36px; margin-right: 20px; }
  .social-icon--pictogram { background: #d8cfc4; }
  .social-icon--friendwall { background: #3b5a96; }
  .social-divider { margin: 0 70px 0 44px; }
</style>
</head>
<body>
  <section class="card card--front" aria-label="Card front">
    <div class="brand-mark"></div>
    <div class="brand-name">Maris Dovey Studio</div>
    <div class="services">
      <span>Dealer</span><span>Curator</span><span>Events</span><span>Styling</span><span>Creative Sourcing</span>
    </div>
  </section>

  <section class="card card--back" aria-label="Card back">
    <div class="back-mark">Maris Dovey<br>Studio</div>
    <h1 class="holder-name">Tessa Varnold</h1>
    <p class="holder-title">Art and Design Consultant</p>
    <div class="rule rule--top"></div>
    <div class="contact">
      <div class="contact-row"><span class="contact-label">Phone :</span><span class="contact-value">0438 217 604</span></div>
      <div class="contact-row"><span class="contact-label">Email&nbsp;&nbsp; :</span><span class="contact-value">tessa@marisdoveystudio.example</span></div>
      <div class="contact-row"><span class="contact-label">Web&nbsp;&nbsp;&nbsp;&nbsp; :</span><span class="contact-value">www.marisdoveystudio.example</span></div>
    </div>
    <div class="rule rule--social-top"></div>
    <div class="social">
      <div class="social-item"><span class="social-icon social-icon--pictogram"></span>MarisDoveyAdviser</div>
      <span class="social-divider">|</span>
      <div class="social-item"><span class="social-icon social-icon--friendwall"></span>marisdoveystudio</div>
    </div>
    <div class="rule rule--social-bottom"></div>
  </section>
</body>
</html>
```